Business Card for a Dental Office

The design should communicate integrity, quality and reliability. We also want the card look elegant, simple, but still stand out, different from the traditional-dental-office business card.

Industry/Entity Type

Business

```html
<!DOCTYPE html>
<html lang="en">
<head>
<meta charset="utf-8">
<title>Halden Dental Centre – Business Card</title>
<link href="https://fonts.googleapis.com/css2?family=Source+Sans+3:wght@400;600;700&display=swap" rel="stylesheet">
<style>
  :root {
    --backdrop: #3b3b3d;
    --card: #0c0c0d;
    --card-panel: #151516;
    --gold: #e9c51a;
    --gold-deep: #b8940a;
    --white: #f4f4f4;
    --muted: #d9d9d9;
  }
  * { box-sizing: border-box; margin: 0; padding: 0; }
  html, body {
    width: 1200px;
    height: 900px;
    overflow: hidden;
    background: var(--backdrop);
    font-family: "Source Sans 3", "Helvetica Neue", Arial, sans-serif;
  }
  .stage {
    position: relative;
    width: 1200px;
    height: 900px;
  }
  .card {
    position: absolute;
    top: 295px;
    width: 540px;
    height: 310px;
    background: var(--card);
    border-radius: 22px;
    overflow: hidden;
    box-shadow: 0 14px 30px rgba(0,0,0,0.45);
  }
  .card--front { left: 45px; }
  .card--back { left: 615px; }

  /* front: brand block */
  .brand-block {
    position: absolute;
    left: 0;
    top: 0;
    width: 270px;
    height: 100%;
    display: flex;
    flex-direction: column;
    align-items: center;
    justify-content: center;
    gap: 16px;
  }
  .brand-square {
    width: 58px;
    height: 58px;
    background: var(--gold);
  }
  .brand-name {
    color: var(--white);
    font-weight: 700;
    font-size: 24px;
    line-height: 1.1;
    letter-spacing: 1px;
    text-align: center;
    text-transform: uppercase;
  }

  /* front: contact panel */
  .contact-panel {
    position: absolute;
    left: 282px;
    top: 0;
    width: 258px;
    height: 100%;
    background: var(--card-panel);
    border-top-left-radius: 18px;
    border-bottom-left-radius: 18px;
    padding: 70px 20px 0 22px;
    color: var(--muted);
  }
  .person-name {
    color: var(--gold);
    font-size: 22px;
    font-weight: 400;
    line-height: 1.1;
  }
  .person-role {
    font-size: 14px;
    color: var(--white);
    margin-top: 2px;
  }
  .address {
    font-size: 14px;
    line-height: 1.25;
    margin-top: 14px;
    color: var(--white);
  }
  .contact-list {
    list-style: none;
    margin-top: 12px;
    font-size: 14px;
    line-height: 1.3;
    color: var(--white);
  }
  .contact-list li {
    display: flex;
    align-items: center;
    gap: 8px;
  }
  .contact-list svg {
    width: 11px;
    height: 11px;
    fill: var(--gold);
    flex: none;
  }

  /* back */
  .back-brand {
    position: absolute;
    left: 0;
    top: 0;
    width: 100%;
    height: 100%;
    display: flex;
    align-items: center;
    justify-content: center;
    gap: 14px;
  }
  .back-brand .brand-square {
    width: 50px;
    height: 50px;
  }
  .back-text { display: flex; flex-direction: column; }
  .back-text .brand-name {
    font-size: 26px;
    text-align: left;
    letter-spacing: 0.5px;
  }
  .tagline {
    color: var(--gold);
    font-size: 11.5px;
    font-weight: 600;
    letter-spacing: 1px;
    text-transform: uppercase;
    margin-top: 2px;
  }
</style>
</head>
<body>
<main class="stage">

  <section class="card card--front" aria-label="Business card front">
    <div class="brand-block">
      <div class="brand-square"></div>
      <div class="brand-name">Halden<br>Dental Centre</div>
    </div>
    <div class="contact-panel">
      <p class="person-name">Daniel Hart</p>
      <p class="person-role">Managing Director</p>
      <p class="address">12345, Address Goes Here<br>Country Name, 123456.</p>
      <ul class="contact-list">
        <li>
          <svg viewBox="0 0 24 24" aria-hidden="true"><path d="M6.6 10.8a15.1 15.1 0 0 0 6.6 6.6l2.2-2.2c.3-.3.7-.4 1-.2 1.1.4 2.3.6 3.6.6.6 0 1 .4 1 1V20c0 .6-.4 1-1 1A17 17 0 0 1 3 4c0-.6.4-1 1-1h3.5c.6 0 1 .4 1 1 0 1.3.2 2.5.6 3.6.1.3 0 .7-.2 1z"/></svg>
          044-123 456 789
        </li>
        <li>
          <svg viewBox="0 0 24 24" aria-hidden="true"><path d="M2 5h20v14H2z" opacity=".9"/><path d="M2 5l10 8 10-8" fill="none" stroke="#151516" stroke-width="2"/></svg>
          info@webname.com
        </li>
        <li>
          <svg viewBox="0 0 24 24" aria-hidden="true"><path d="M10.6 13.4a1 1 0 0 1 0-1.4l3.5-3.5a1 1 0 1 1 1.4 1.4L12 13.4a1 1 0 0 1-1.4 0zM8 11l-3 3a3.5 3.5 0 0 0 5 5l3-3 1.4 1.4-3 3A5.5 5.5 0 0 1 3.6 12.6l3-3zm8 2l3-3a3.5 3.5 0 0 0-5-5l-3 3-1.4-1.4 3-3a5.5 5.5 0 0 1 7.8 7.8l-3 3z"/></svg>
          www.websitename.com
        </li>
      </ul>
    </div>
  </section>

  <section class="card card--back" aria-label="Business card back">
    <div class="back-brand">
      <div class="brand-square"></div>
      <div class="back-text">
        <span class="brand-name">Halden Dental Centre</span>
        <span class="tagline">Your smile is your gift to others</span>
      </div>
    </div>
  </section>

</main>
</body>
</html>
```